design a construction company business card

Design business card around our logo. Card must have all the typical info: name, title, address, phone, email, business name, etc. Somewhere on the card I would like to see our motto "Built on integrity... Inspired by commitment." Consider adding a splash of bright orange to the card to complement the blues and silvers/grays in the logo. We are open to metallic inks, textures, etc. We would like to see options on both light and dark backgrounds. The font in the logo is Euro Technic Extended Regular.

```html
<!DOCTYPE html>
<html lang="en">
<head>
<meta charset="utf-8">
<title>Dalton Contracting – Business Card</title>
<link rel="stylesheet" href="https://fonts.googleapis.com/css2?family=Roboto:ital,wght@0,400;0,500;0,700;1,400&display=swap">
<style>
  :root {
    --page-bg: #ecebe8;
    --brand-blue: #2a3c94;
    --brand-blue-light: #1a6fc0;
    --brand-gray: #808184;
    --card-white: #ffffff;
    --text-light: #ffffff;
    --text-muted: #4a4a4c;
    --card-shadow: 0 4px 10px rgba(0, 0, 0, 0.35);
  }
  * { margin: 0; padding: 0; box-sizing: border-box; }
  html, body {
    width: 1125px;
    height: 1200px;
    overflow: hidden;
    background: var(--page-bg);
    font-family: "Roboto", Arial, sans-serif;
  }
  .card {
    position: absolute;
    left: 171px;
    width: 826px;
    height: 471px;
    box-shadow: var(--card-shadow);
    overflow: hidden;
  }
  .card--front {
    top: 106px;
    background: radial-gradient(circle at 60% 40%, var(--brand-blue-light) 0%, var(--brand-blue) 62%);
  }
  .card--back {
    top: 639px;
    background: var(--card-white);
  }
  .side-band {
    position: absolute;
    top: 0;
    right: 0;
    width: 229px;
    height: 100%;
    background: var(--brand-gray);
  }
  .front-content {
    position: absolute;
    left: 60px;
    top: 68px;
    color: var(--text-light);
  }
  .company-name {
    font-weight: 700;
    font-size: 44px;
    letter-spacing: 2px;
    line-height: 1;
    text-transform: uppercase;
  }
  .company-name span { display: block; font-size: 17px; letter-spacing: 3px; margin-top: 10px; }
  .person-name {
    margin-top: 68px;
    font-weight: 700;
    font-size: 28px;
    letter-spacing: 0.5px;
  }
  .person-title {
    margin-top: 6px;
    font-size: 19px;
    letter-spacing: 0.5px;
  }
  .address {
    margin-top: 20px;
    font-size: 18px;
    line-height: 26px;
    font-style: normal;
    letter-spacing: 0.3px;
  }
  .contact-list {
    list-style: none;
    margin-top: 14px;
    font-size: 18px;
    letter-spacing: 0.3px;
  }
  .contact-list li {
    display: flex;
    align-items: center;
    gap: 8px;
    height: 26px;
  }
  .contact-list svg { width: 18px; height: 18px; fill: var(--text-light); flex: none; }
  .back-brand {
    position: absolute;
    top: 200px;
    left: 0;
    width: 100%;
    text-align: center;
    color: var(--brand-blue);
    font-weight: 700;
    font-size: 52px;
    letter-spacing: 3px;
    line-height: 1;
    text-transform: uppercase;
  }
  .back-brand span { display: block; font-size: 20px; letter-spacing: 4px; margin-top: 12px; }
  .motto {
    position: absolute;
    top: 400px;
    left: 0;
    width: 100%;
    text-align: center;
    font-style: italic;
    font-size: 19px;
    color: var(--text-muted);
  }
</style>
</head>
<body>
  <section class="card card--front">
    <div class="side-band"></div>
    <div class="front-content">
      <div class="company-name">Dalton<span>Contracting, Inc.</span></div>
      <div class="person-name">MARCUS HALE</div>
      <div class="person-title">CEO/FOUNDER</div>
      <address class="address">4120 Birchwood Road<br>Fairbanks, Alaska 99701</address>
      <ul class="contact-list">
        <li>
          <svg viewBox="0 0 24 24" aria-hidden="true"><path d="M6.6 10.8a15.1 15.1 0 0 0 6.6 6.6l2.2-2.2a1 1 0 0 1 1-.25 11.4 11.4 0 0 0 3.6.57 1 1 0 0 1 1 1V20a1 1 0 0 1-1 1A17 17 0 0 1 3 4a1 1 0 0 1 1-1h3.5a1 1 0 0 1 1 1c0 1.25.2 2.45.57 3.57a1 1 0 0 1-.25 1z"/></svg>
          907 555 0182
        </li>
        <li>
          <svg viewBox="0 0 24 24" aria-hidden="true"><path d="M2 5h20v14H2z M4 7v.5l8 5 8-5V7l-8 5z" fill-rule="evenodd"/></svg>
          marcus@daltonbuild.com
        </li>
        <li>
          <svg viewBox="0 0 24 24" aria-hidden="true"><path d="M12 2a10 10 0 1 0 0 20 10 10 0 0 0 0-20zm-1 17.9A8 8 0 0 1 4.2 10.4L9 15v1a2 2 0 0 0 2 2zm6.9-2.5A2 2 0 0 0 16 16h-1v-3a1 1 0 0 0-1-1H8v-2h2a1 1 0 0 0 1-1V7h2a2 2 0 0 0 2-2v-.4a8 8 0 0 1 2.9 12.8z"/></svg>
          www.daltonbuild.com
        </li>
      </ul>
    </div>
  </section>

  <section class="card card--back">
    <div class="back-brand">Dalton<span>Contracting, Inc.</span></div>
    <p class="motto">Built on integrity... Inspired by commitment.</p>
  </section>
</body>
</html>
```